Corvane Holdings , new business card design

investment firm with corporate clients . need double sided business card , vertical and horizontal options ,logo must be clear. prefer pantone colors only and sharp design. website also www.corvane.ae

Khalid Bin Tarrafi
Managing Director
Tel. +971 4 387 2940
Mobile +971 50 518 2403
khalid@corvane.ae
Q-Span Plaza, officw 18-B07, Warqa Gardens, Dubai

Contact Information for Business Card

Khalid Bin Tarrafi
Managing Director

Font styles to use
Serif

Colors

Designer to choose colors to be used in the design.

```html
<!DOCTYPE html>
<html lang="en">
<head>
<meta charset="utf-8">
<title>Corvane Holdings — Business Card</title>
<link href="https://fonts.googleapis.com/css2?family=Jost:wght@300;400&display=swap" rel="stylesheet">
<style>
  :root {
    --backdrop: #cdd3d3;
    --paper: #f1f1ef;
    --ink: #1c1c1c;
    --brand-blue: #2d5f8e;
    --edge-blue: #1f4f86;
  }
  html, body {
    margin: 0;
    width: 1200px;
    height: 1200px;
    overflow: hidden;
    background: var(--backdrop);
    font-family: "Jost", "Futura", sans-serif;
  }
  .canvas {
    position: relative;
    width: 1200px;
    height: 1200px;
  }
  .card {
    position: absolute;
    width: 730px;
    height: 420px;
    background: var(--paper);
    box-sizing: border-box;
  }
  /* Brand side */
  .card--brand {
    left: 400px;
    top: 110px;
    border-bottom: 6px solid var(--edge-blue);
    display: flex;
    align-items: center;
    justify-content: center;
  }
  .wordmark {
    display: flex;
    align-items: center;
    gap: 18px;
    color: var(--ink);
    font-weight: 300;
    text-transform: uppercase;
    line-height: 1;
  }
  .wordmark__square {
    width: 18px;
    height: 18px;
    background: var(--brand-blue);
    flex: none;
  }
  .card--brand .wordmark__name {
    font-size: 44px;
    letter-spacing: 12px;
  }
  /* Contact side */
  .card--contact {
    left: 70px;
    top: 640px;
    padding: 44px 40px;
  }
  .card--contact .wordmark {
    position: absolute;
    top: 58px;
    right: 40px;
    gap: 10px;
  }
  .card--contact .wordmark__square {
    width: 10px;
    height: 10px;
  }
  .card--contact .wordmark__name {
    font-size: 20px;
    letter-spacing: 5px;
  }
  .contact {
    margin-top: 120px;
    color: var(--ink);
    text-transform: uppercase;
    font-weight: 400;
  }
  .contact__name {
    font-size: 21px;
    letter-spacing: 1.5px;
    color: var(--brand-blue);
    margin: 0;
  }
  .contact__title {
    font-size: 16px;
    text-transform: none;
    margin: 2px 0 0;
  }
  .rule {
    width: 150px;
    height: 2px;
    background: var(--brand-blue);
    margin: 10px 0;
  }
  .contact__line {
    font-size: 17px;
    letter-spacing: 1.6px;
    margin: 0 0 4px;
  }
</style>
</head>
<body>
<main class="canvas">
  <section class="card card--brand" aria-label="Card front">
    <div class="wordmark">
      <span class="wordmark__square"></span>
      <span class="wordmark__name">Corvane Holdings</span>
    </div>
  </section>

  <section class="card card--contact" aria-label="Card back">
    <div class="wordmark">
      <span class="wordmark__square"></span>
      <span class="wordmark__name">Corvane Holdings</span>
    </div>
    <div class="contact">
      <p class="contact__name">Khalid Bin Tarrafi</p>
      <p class="contact__title">Managing Director</p>
      <div class="rule"></div>
      <p class="contact__line">Q-Span Plaza, officw 18-B07, Warqa Gardens, Dubai</p>
      <div class="rule"></div>
      <p class="contact__line">P: +971 4 387 2940 | M: +971 50 518 2403</p>
      <p class="contact__line">E: khalid@corvane.ae</p>
    </div>
  </section>
</main>
</body>
</html>
```